Business Card Design for BrightvaleMedia.com

--I need a business card design for my company BrightvaleMedia.com

I have attached my logo...I want the brightvale media logo on the front of the business card, and then I want The Quillstone Chief on the back of it with my information.

I would like to see a light colored background as well as a dark colored background

FRONT:
BRIGHTVALE MEDIA LOGO
248 N. Larkmoor
3rd Floor
San Diego CA 92173
www.BrightvaleMedia.com

Advanced Website & App Development
Websites, Apps, Online Voucher Systems

Leading Edge Marketing Services
SMS, VB, SMM, SEM,

BACK:
QUILLSTONE CHIEF LOGO
Dorian Pelletta
The Quillstone Chief
Call Or Text: 619-555-0148
Dorian@QuillstoneChief.example
www.QuillstoneChief.example

Target Market(s)

small business owners

Industry/Entity Type

Business Consultant

Contact Information for Business Card

FRONT:
BRIGHTVALE MEDIA LOGO
248 N. Larkmoor
3rd Floor
San Diego CA 92173
www.BrightvaleMedia.com

SMS, VB, SMM, SEM,

BACK:
QUILLSTONE CHIEF LOGO
Dorian Pelletta
The Quillstone Chief
Dorian@QuillstoneChief.example
www.QuillstoneChief.example

Requirements
Must have
• add this quote on it somewhere, anywhere,preferrably on back
• "The Fastest Way To Success Is To Take Action”
• — Dorian Pelletta, Quillstone Chief
Nice to have
• open
Should not have
• red

```html
<!DOCTYPE html>
<html lang="en">
<head>
<meta charset="utf-8">
<title>Brightvale Media – Business Card</title>
<link rel="stylesheet" href="https://fonts.googleapis.com/css2?family=Open+Sans:wght@400;600&display=swap">
<style>
  :root {
    --brand-blue: #0b6aa6;
    --ink: #4d4f52;
    --card: #ffffff;
    --stage: #4b4b4d;
  }
  html, body {
    margin: 0;
    padding: 0;
    width: 1105px;
    height: 1200px;
    overflow: hidden;
    background: var(--stage);
    font-family: "Open Sans", Arial, sans-serif;
  }
  .card {
    position: absolute;
    left: 196px;
    width: 720px;
    height: 412px;
    background: var(--card);
    overflow: hidden;
  }
  .card--front { top: 146px; }
  .card--back { top: 602px; }

  /* Front */
  .wordmark {
    position: absolute;
    left: 0;
    width: 100%;
    top: 74px;
    margin: 0;
    text-align: center;
    color: var(--brand-blue);
    font-weight: 600;
    line-height: 1;
  }
  .wordmark__main { display: block; font-size: 54px; letter-spacing: 7px; padding-left: 7px; }
  .wordmark__sub { display: block; font-size: 21px; letter-spacing: 8px; padding-left: 8px; margin-top: 10px; }

  .services {
    position: absolute;
    left: 0;
    width: 100%;
    text-align: center;
    color: var(--ink);
    font-size: 19.5px;
    line-height: 27px;
    margin: 0;
  }
  .services--web { top: 186px; }
  .services--marketing { top: 266px; }
  .address {
    position: absolute;
    left: 0; width: 100%;
    top: 334px;
    text-align: center;
    color: var(--ink);
    font-size: 19.5px;
    margin: 0;
  }
  .dot { color: var(--brand-blue); padding: 0 3px; }
  .web-rule {
    position: absolute;
    left: 0; right: 0;
    top: 376px;
    height: 2px;
    background: var(--brand-blue);
  }
  .web-link {
    position: absolute;
    left: 50%;
    top: 362px;
    transform: translateX(-50%);
    background: var(--card);
    padding: 0 8px;
    color: var(--brand-blue);
    font-weight: 600;
    font-size: 19.5px;
    white-space: nowrap;
  }

  /* Back */
  .band { position: absolute; left: 0; top: 0; }
  .chief-mark {
    position: absolute;
    right: 54px;
    top: 56px;
    margin: 0;
    color: #ffffff;
    font-weight: 600;
    text-align: right;
    line-height: 1;
  }
  .chief-mark__main { display: block; font-size: 44px; letter-spacing: 5px; margin-right: -5px; }
  .chief-mark__sub { display: block; font-size: 18px; letter-spacing: 7px; margin-right: -7px; margin-top: 8px; }

  .contact {
    position: absolute;
    left: 50px;
    top: 286px;
    margin: 0;
    padding: 0;
    list-style: none;
    color: var(--ink);
    font-size: 19px;
  }
  .contact li { display: flex; align-items: center; height: 27.5px; }
  .contact svg { width: 18px; height: 18px; margin-right: 10px; fill: var(--brand-blue); }

  .person {
    position: absolute;
    right: 52px;
    top: 296px;
    text-align: right;
  }
  .person__name { margin: 0; color: var(--brand-blue); font-weight: 600; font-size: 25px; line-height: 32px; }
  .person__title { margin: 0; color: var(--ink); font-size: 19.5px; line-height: 28px; }

  .quote {
    position: absolute;
    left: 0;
    width: 100%;
    top: 380px;
    margin: 0;
    text-align: center;
    color: var(--ink);
    font-size: 13.5px;
    line-height: 18px;
    white-space: nowrap;
  }
  .quote__author { color: var(--brand-blue); font-weight: 600; }
</style>
</head>
<body>

<section class="card card--front" aria-label="Front of card">
  <h1 class="wordmark">
    <span class="wordmark__main">BRIGHTVALE</span>
    <span class="wordmark__sub">MEDIA</span>
  </h1>
  <p class="services services--web">
    Advanced Website &amp; App Development<br>
    Websites<span class="dot">•</span>Apps<span class="dot">•</span>Online Voucher Systems
  </p>
  <p class="services services--marketing">
    Leading Edge Marketing Services<br>
    SMS<span class="dot">•</span>VB<span class="dot">•</span>SMM<span class="dot">•</span>SEM
  </p>
  <p class="address">248 N. Larkmoor, 3rd Floor, San Diego CA 92173</p>
  <div class="web-rule"></div>
  <span class="web-link">www.BrightvaleMedia.com</span>
</section>

<section class="card card--back" aria-label="Back of card">
  <svg class="band" width="720" height="260" viewBox="0 0 720 260" aria-hidden="true">
    <polygon points="0,0 720,0 720,248 343,248 308,213 0,213" fill="var(--brand-blue)"/>
    <line x1="324" y1="233" x2="720" y2="233" stroke="#ffffff" stroke-width="4"/>
  </svg>

  <h2 class="chief-mark">
    <span class="chief-mark__main">QUILLSTONE</span>
    <span class="chief-mark__sub">CHIEF</span>
  </h2>

  <ul class="contact">
    <li>
      <svg viewBox="0 0 24 24" aria-hidden="true"><path d="M6.6 10.8a15.1 15.1 0 0 0 6.6 6.6l2.2-2.2c.3-.3.7-.4 1-.2 1.1.4 2.3.6 3.6.6.6 0 1 .4 1 1V20c0 .6-.4 1-1 1A17 17 0 0 1 3 4c0-.6.4-1 1-1h3.5c.6 0 1 .4 1 1 0 1.3.2 2.5.6 3.6.1.3 0 .7-.2 1z"/></svg>
      619-555-0148
    </li>
    <li>
      <svg viewBox="0 0 24 24" aria-hidden="true"><path d="M2 5h20v14H2z"/><path d="M3 6l9 7 9-7" fill="none" stroke="#fff" stroke-width="1.6"/></svg>
      Dorian@QuillstoneChief.example
    </li>
    <li>
      <svg viewBox="0 0 24 24" aria-hidden="true"><circle cx="12" cy="12" r="10"/><path d="M2 12h20M12 2c3 3 3 17 0 20M12 2c-3 3-3 17 0 20" fill="none" stroke="#fff" stroke-width="1.4"/></svg>
      www.QuillstoneChief.example
    </li>
  </ul>

  <div class="person">
    <p class="person__name">Dorian Pelletta</p>
    <p class="person__title">The Quillstone Chief</p>
  </div>

  <p class="quote">“The Fastest Way To Success Is To Take Action” <span class="quote__author">— Dorian Pelletta, Quillstone Chief</span></p>
</section>

</body>
</html>
```